Heron Property Inspection business card

I am the principal inspector of Heron Property Inspections. I serve Northern Virginia from Winchester to Arlington.Associate, Federated Guild of Dwelling Examiners (FGDE)Graduate, FGDE Home Inspectors CourseNational Association of Home Inspectors ExamI'd like the business card to look more professional than comical.I pulled the attached picture off the web. I'd like to have something like that or an image of a house as my logo on the cards.

Target Market(s)

Persons who recently purchased a home.

Industry/Entity Type

Business

Contact Information for Business Card

Bob AllenBadger Home Inspections, LLC.4455 River RoadBluemont, Virginia 20135cell: 703-231-6680e-mail: tkmarlow@postvale.net

Font styles to use
Serif
Sans Serif

Requirements
Must have
• I'd like to have a logo, something that identifies me as a home inspector. The attached images are something that I'd like to have incorporated into my business card logo.
Nice to have
• I'd like a sketch of a house and/or a magnifying glass showing a house being inspected. The attached images are used as a suggestion only, I do not own the images.
Should not have
• Gimmicky stuff. I want to appear professional and trustworthy.

```html
<!DOCTYPE html>
<html lang="en">
<head>
<meta charset="utf-8">
<title>Heron Property Inspections – Business Card</title>
<link rel="stylesheet" href="https://fonts.googleapis.com/css2?family=Montserrat:wght@500;700&family=Open+Sans:wght@400;600&display=swap">
<style>
  :root {
    --canvas: #e3e1de;
    --card: #ffffff;
    --navy: #233f8a;
    --sky: #3aa7dd;
    --ink: #555659;
    --text: #333438;
    --shadow: rgba(0, 0, 0, 0.14);
  }
  * { box-sizing: border-box; margin: 0; padding: 0; }
  html, body {
    width: 1200px;
    height: 1189px;
    overflow: hidden;
    background: var(--canvas);
  }
  .canvas {
    width: 1200px;
    height: 1189px;
    display: flex;
    flex-direction: column;
    align-items: center;
    justify-content: center;
    gap: 60px;
  }
  .card {
    position: relative;
    width: 900px;
    height: 514px;
    background: var(--card);
    box-shadow: 0 6px 18px var(--shadow);
    overflow: hidden;
  }

  /* Wordmark: one line, one colour, one weight */
  .wordmark {
    display: flex;
    align-items: center;
    gap: 14px;
    white-space: nowrap;
  }
  .wordmark__dot {
    border-radius: 50%;
    background: var(--sky);
    flex: none;
  }
  .wordmark__name {
    font-family: "Montserrat", sans-serif;
    font-weight: 700;
    color: var(--ink);
    letter-spacing: 0.2px;
  }

  .card--front {
    display: flex;
    align-items: center;
    justify-content: center;
  }
  .card--front .wordmark__name { font-size: 34px; }
  .card--front .wordmark__dot { width: 40px; height: 40px; }

  /* Back */
  .card--back .brand-area {
    position: absolute;
    left: 0;
    top: 120px;
    width: 470px;
    height: 220px;
    display: flex;
    align-items: center;
    justify-content: center;
  }
  .card--back .wordmark { gap: 10px; }
  .card--back .wordmark__name { font-size: 18px; }
  .card--back .wordmark__dot { width: 24px; height: 24px; }
  .divider {
    position: absolute;
    left: 470px;
    top: 40px;
    width: 1px;
    height: 340px;
    background: var(--navy);
    opacity: 0.7;
  }
  .contact {
    position: absolute;
    left: 520px;
    top: 70px;
  }
  .contact__name {
    font-family: "Montserrat", sans-serif;
    font-weight: 700;
    font-size: 36px;
    color: var(--ink);
  }
  .contact__role {
    font-family: "Montserrat", sans-serif;
    font-weight: 500;
    font-size: 22px;
    color: var(--navy);
    margin-top: 2px;
  }
  .contact__list {
    list-style: none;
    margin-top: 62px;
    font-family: "Open Sans", sans-serif;
    font-size: 21px;
    color: var(--text);
  }
  .contact__item {
    display: flex;
    align-items: center;
    gap: 10px;
    margin-bottom: 6px;
  }
  .contact__icon { width: 22px; height: 22px; flex: none; }
  .address-band {
    position: absolute;
    left: 0;
    right: 0;
    bottom: 0;
    height: 112px;
    background: var(--navy);
    color: #ffffff;
    font-family: "Open Sans", sans-serif;
    font-weight: 600;
    font-size: 31px;
    display: flex;
    align-items: center;
    justify-content: center;
    letter-spacing: 0.3px;
  }
</style>
</head>
<body>
<main class="canvas">

  <section class="card card--front" aria-label="Business card front">
    <div class="wordmark">
      <span class="wordmark__dot"></span>
      <span class="wordmark__name">Heron Property Inspections, LLC</span>
    </div>
  </section>

  <section class="card card--back" aria-label="Business card back">
    <div class="brand-area">
      <div class="wordmark">
        <span class="wordmark__dot"></span>
        <span class="wordmark__name">Heron Property Inspections, LLC</span>
      </div>
    </div>

    <div class="divider"></div>

    <div class="contact">
      <p class="contact__name">Employee Name</p>
      <p class="contact__role">Managing Director</p>
      <ul class="contact__list">
        <li class="contact__item">
          <svg class="contact__icon" viewBox="0 0 22 22" aria-hidden="true">
            <rect width="22" height="22" rx="2" fill="#233f8a"/>
            <rect x="7" y="4" width="8" height="14" rx="1.5" fill="none" stroke="#fff" stroke-width="1.6"/>
            <circle cx="11" cy="15.3" r="1" fill="#fff"/>
          </svg>
          <span>703-555-0192</span>
        </li>
        <li class="contact__item">
          <svg class="contact__icon" viewBox="0 0 22 22" aria-hidden="true">
            <rect width="22" height="22" rx="2" fill="#233f8a"/>
            <rect x="4" y="6" width="14" height="10" fill="none" stroke="#fff" stroke-width="1.6"/>
            <polyline points="4,6 11,12 18,6" fill="none" stroke="#fff" stroke-width="1.6"/>
          </svg>
          <span>tkmarlow@postvale.net</span>
        </li>
      </ul>
    </div>

    <div class="address-band">7182 Quarry Lane Fernhill, Virginia 20148</div>
  </section>

</main>
</body>
</html>
```